Corwin Beacon Lighting - Commercial & Residential Landscape Lighting

Landscape Lighting Services & Design: Create a website for our landscape lighting company. We would like the design to be tailored around this description:
Illuminate with Confidence. Designed with Precision. Installed with Care.
Locally and veteran-owned, we take pride in transforming outdoor spaces through innovative lighting solutions tailored to your vision. From landscape and holiday lighting to permanent installations, our effortless process and expert design deliver breathtaking results and lasting curb appeal. Backed by a lifetime warranty and quarterly service options, our commitment to quality and customer satisfaction is unwavering. Try before you buy and experience your home in a whole new light with our complimentary demo kit — see the stunning effects before you decide.
- Also, add in this information as well; Outdoor Lighting not only beautifies spaces but also significantly enhances safety by illuminating your home or business. Beautifully lit entrances deter potential intruders, making your home a safer place for your loved ones. we also offer quarterly service plans to ensure lighting equipment continues to operate & illuminate effectively throughout the year. Also mention we provide free estimates and we are offering a 10% discount to military, veterans, and first responders.

Target Market(s)

Luxury market

Industry/Entity Type

Landscape Lighting - Residential & Commercial Lighting Services

Coding

Coded - Design and coding required

Number of Pages Required

2 page

Colors
00AB8E
00BBA5
67D7C9
C6EFE9
E9F9F6
59FF00
82FF00
B8FF75
E3FFCB
F4FFEA
FFC000
F8CF3A
FAE287
FDF2CF
FEFAEE

Requirements
Must have
• a lead generation button where people can submit their information for us to reach out to them and schedule their free estimate, homepage, about page, contact page, products and services page, user friendly, easy to navigate, and it also must be engaging and eye popping, as well as appealing to the luxury market. Please use colors; verdent green, dark green, ivory, and sunny yellow. Also, include an about page that references our story; Derek is retired Army and he opened a fitness studio in 2017 with his wife Jolene. He has installed low voltage lighting in every home he lived in and for his friends and family over the years and decided to open his own business because he is passionate about beautifying outdoor landscapes and highlighting a properties full potential, not only in the day but at night as well all while providing safety and security for his clients. Having a deep respect for nature and landscaping, he wants to provide the same care and quality to each of his clients as he has in the fitness industry for decades. He believes small businesses are the back bone of America and he's excited to provide a service that is all to often neglected in the design of a home.
Nice to have
• I would like to have a clear intent and purpose, engaging web design, clear call to action, optimized for search engines, mobile friendy design, security measures, credibility indicators

```html
<!DOCTYPE html>
<html lang="en">
<head>
<meta charset="utf-8">
<title>Corwin Beacon Lighting — Landscape Lighting</title>
<link href="https://fonts.googleapis.com/css2?family=Poppins:wght@300;400;500;600;700&display=swap" rel="stylesheet">
<style>
:root{
  --teal:#00AB8E;
  --teal-light:#00BBA5;
  --mint:#E9F9F6;
  --yellow:#FFC000;
  --yellow-soft:#F8CF3A;
  --ivory:#FCF3D3;
  --ink:#141414;
  --dark:#0d1512;
  --dark-2:#111a16;
  --white:#ffffff;
  --grey:#6b6b6b;
}
*{box-sizing:border-box;margin:0;padding:0}
html,body{width:1200px;height:3814px;overflow:hidden}
body{font-family:"Poppins",sans-serif;color:var(--ink);background:var(--white);position:relative}
a{color:inherit;text-decoration:none}

/* header */
.site-header{position:absolute;left:0;top:0;width:1200px;height:56px;background:#fff;box-shadow:0 1px 4px rgba(0,0,0,.08);z-index:3}
.brand{position:absolute;left:121px;top:18px;font-size:14px;font-weight:600;color:#c8283a;letter-spacing:.5px;white-space:nowrap}
.main-nav{position:absolute;left:390px;top:20px;display:flex;gap:22px;font-size:11px;letter-spacing:.6px}
.main-nav a.active{color:var(--teal);border-bottom:2px solid var(--teal);padding-bottom:4px}
.phone{position:absolute;left:832px;top:15px;display:flex;align-items:center;gap:12px;font-size:12px;font-weight:600;white-space:nowrap}
.phone .ico{width:26px;height:26px;background:var(--teal);display:flex;align-items:center;justify-content:center}
.btn{display:inline-block;background:var(--yellow);color:#fff;font-weight:600;font-size:11px;letter-spacing:1px;text-align:center;white-space:nowrap}
.book{position:absolute;left:980px;top:13px;width:98px;height:30px;line-height:30px}

/* hero */
.hero{position:absolute;left:0;top:56px;width:1200px;height:603px;background:linear-gradient(180deg,#1a2c4e 0%,#34496b 35%,#6c6048 62%,#2f3b22 80%,#3f5a24 100%)}
.hero h1{position:absolute;top:70px;width:100%;text-align:center;font-size:46px;font-weight:500;color:#fff;letter-spacing:.5px}
.hero h1 span{color:var(--yellow)}
.hero p{position:absolute;top:126px;width:100%;text-align:center;font-size:12px;color:#fff}

/* category cards */
.cat{position:absolute;top:726px;height:259px}
.cat-photo{position:absolute;top:726px;width:195px;height:259px}
.cat h2{font-size:22px;font-weight:500;letter-spacing:2px;color:#fff;margin-bottom:4px}
.cat ul{list-style:none;font-size:13px;color:#fff;line-height:26px;white-space:nowrap}
.cat li::before{content:"•";margin-right:8px}
.cat .cat-btn{display:inline-block;margin-top:12px;background:#fff;color:var(--ink);font-size:11px;font-weight:600;padding:12px 14px;letter-spacing:.4px;white-space:nowrap}
.cat-res{left:316px;width:275px;background:var(--teal);padding:34px 20px 0 30px}
.cat-com{left:609px;width:275px;background:var(--yellow);padding:34px 10px 0 55px}
.cat-com ul{font-size:12px}
.badge{position:absolute;left:549px;top:810px;width:92px;height:92px;border-radius:50%;background:#fff;border:4px solid var(--yellow);display:flex;align-items:center;justify-content:center;text-align:center;font-size:10px;font-weight:600;color:#c8283a;line-height:13px;z-index:2}

/* about */
.watermark-v{position:absolute;left:50px;top:1500px;transform:rotate(-90deg);transform-origin:left top;font-size:150px;font-weight:300;color:rgba(0,0,0,.05);letter-spacing:6px;white-space:nowrap}
.about{position:absolute;left:121px;top:1110px;width:440px}
.about h2{font-size:30px;font-weight:500;display:flex;align-items:center;gap:6px}
.about h2::after{content:"";width:52px;height:2px;background:var(--teal)}
.about p{font-size:11.5px;line-height:19px;color:#333;margin-top:12px}
.about .btn{margin-top:18px;padding:10px 14px}
.about-frame{position:absolute;left:766px;top:1049px;width:312px;height:385px;border:2px solid var(--teal)}
.about-photo{position:absolute;left:615px;top:1062px;width:449px;height:360px;background:linear-gradient(160deg,#2a3a4a 0%,#6e6556 35%,#d6ad62 55%,#2f4a20 80%,#1c2c14 100%)}

/* stats */
.stats{position:absolute;left:0;top:1496px;width:1200px;height:237px;background:linear-gradient(90deg,#0f1410,#1c231a 50%,#0f1410)}
.stat{position:absolute;top:34px;width:200px;text-align:center;color:#fff}
.stat .ring{width:82px;height:82px;margin:0 auto;border-radius:50%;background:#fff;border:5px solid var(--teal);display:flex;align-items:center;justify-content:center}
.stat .num{font-size:34px;font-weight:600;color:var(--teal);margin-top:10px;line-height:40px}
.stat .lbl{font-size:17px;line-height:22px}
.divider{position:absolute;top:52px;height:145px;border-left:1px dashed rgba(255,255,255,.45)}

/* services */
.section-title{position:absolute;width:100%;text-align:center;font-size:29px;font-weight:500}
.svc{position:absolute;top:1856px;width:307px;height:320px;background:#0d0d0d}
.svc .ph{height:245px}
.svc .label{position:absolute;left:0;top:260px;height:48px;width:100%;border-left:4px solid var(--yellow);color:#fff;font-size:14.5px;font-weight:600;letter-spacing:1.4px;display:flex;align-items:center;justify-content:center;white-space:nowrap}

/* projects */
.slide{position:absolute;top:2282px;height:392px}
.proj-label{position:absolute;bottom:0;width:175px;height:41px;background:#c9c9c9;color:#333;font-size:14px;letter-spacing:1.5px;font-weight:500;display:flex;align-items:center;justify-content:center}
.arrow{position:absolute;top:2462px;width:32px;height:32px;border-radius:50%;border:1.5px solid #fff;display:flex;align-items:center;justify-content:center}
.explore{position:absolute;left:510px;top:2705px;width:180px;height:36px;line-height:36px}

/* testimonial */
.quote-box{position:absolute;left:121px;top:2807px;width:479px;height:341px;background:var(--ivory);text-align:center}
.quote-mark{position:absolute;left:170px;top:-10px;font-size:240px;line-height:240px;color:#e3d8b2;font-weight:700}
.stars{position:absolute;top:95px;width:100%;color:#f0b400;font-size:14px;letter-spacing:3px}
.q-name{position:absolute;top:118px;width:100%;font-size:12.5px;font-weight:600}
.q-role{position:absolute;top:137px;width:100%;font-size:12.5px;color:var(--grey)}
.q-text{position:absolute;top:165px;left:60px;width:360px;font-size:12.5px;line-height:19px;color:#333}
.quote-photo{position:absolute;left:600px;top:2807px;width:477px;height:341px;background:linear-gradient(135deg,#dcecef 0%,#b9dde0 60%,#9dcfd3 100%)}
.play{position:absolute;left:202px;top:132px;width:72px;height:72px;border-radius:50%;border:2px solid #fff;background:rgba(255,255,255,.35);display:flex;align-items:center;justify-content:center}

/* cta */
.cta{position:absolute;left:0;top:3210px;width:1200px;height:242px;background:linear-gradient(180deg,#0f1717 0%,#232a2a 45%,#3a3324 70%,#1b2318 100%);text-align:center;color:#fff}
.cta h2{margin-top:66px;font-size:30px;font-weight:500;letter-spacing:.5px}
.cta p{font-size:12px;margin-top:6px}
.cta .btn{margin-top:18px;padding:10px 14px}

/* footer */
.footer{position:absolute;left:0;top:3452px;width:1200px;height:362px;background:var(--dark);color:#fff;overflow:hidden}
.f-brand{position:absolute;left:121px;top:62px;font-size:16px;font-weight:500;letter-spacing:1px;white-space:nowrap}
.f-about{position:absolute;left:121px;top:120px;width:245px;font-size:11.5px;line-height:19px}
.socials{position:absolute;left:121px;top:208px;display:flex;gap:10px}
.socials span{width:29px;height:29px;border-radius:50%;background:var(--yellow)}
.f-head{position:absolute;top:70px;font-size:19px;font-weight:500;white-space:nowrap}
.f-menu{position:absolute;left:440px;top:114px;list-style:none;font-size:11.5px;line-height:23px}
.f-contact{position:absolute;left:588px;top:114px;width:250px;font-size:11.5px;line-height:15px}
.f-contact div{display:flex;gap:12px;margin-bottom:16px;align-items:flex-start}
.f-contact .ci{flex:none;width:26px;height:26px;border-radius:50%;background:var(--yellow);display:flex;align-items:center;justify-content:center}
.f-news{position:absolute;left:872px;top:112px;width:206px;font-size:11.5px}
.f-news .field{margin-top:10px;border:1px solid #fff;height:28px;line-height:26px;padding-left:22px;font-size:10.5px}
.f-news .btn{margin-top:14px;width:104px;height:32px;line-height:32px}
.copyright{position:absolute;top:278px;width:100%;text-align:center;font-size:11.5px}
.f-watermark{position:absolute;left:0;top:300px;font-size:78px;font-weight:500;color:rgba(255,255,255,.05);white-space:nowrap;letter-spacing:2px}
</style>
</head>
<body>

<header class="site-header">
  <div class="brand">CORWIN BEACON LIGHTING</div>
  <nav class="main-nav">
    <a class="active" href="#">HOME</a><a href="#">SERVICES</a><a href="#">PORTFOLIO</a><a href="#">ABOUT</a><a href="#">CONTACT</a>
  </nav>
  <div class="phone">
    <span class="ico"><svg width="13" height="13" viewBox="0 0 24 24" fill="#fff"><path d="M6.6 10.8a15 15 0 0 0 6.6 6.6l2.2-2.2a1 1 0 0 1 1-.25 11.4 11.4 0 0 0 3.6.57 1 1 0 0 1 1 1V20a1 1 0 0 1-1 1A17 17 0 0 1 3 4a1 1 0 0 1 1-1h3.5a1 1 0 0 1 1 1c0 1.25.2 2.45.57 3.57a1 1 0 0 1-.25 1z"/></svg></span>
    61 400 555 017
  </div>
  <a class="btn book" href="#">BOOK NOW</a>
</header>

<section class="hero" role="img" aria-label="Modern home at dusk with lit windows and a lantern-lined paver driveway">
  <h1><span>LIGHT UP</span> YOUR LANDSCAPE</h1>
  <p>Premium outdoor lighting for homes, gardens, and commercial properties—designed and installed by experts.</p>
</section>

<div class="cat-photo" style="left:121px;background:linear-gradient(160deg,#1e2a20,#6a5430 45%,#c79a5a 70%,#3d3226)" role="img" aria-label="Garden path under string lights with a lantern"></div>
<div class="cat cat-res">
  <h2>RESIDENTIAL</h2>
  <ul><li>Garden Lighting</li><li>Pathway Lighting</li><li>Security Lighting</li><li>Pool &amp; Patio Lighting</li></ul>
  <a class="cat-btn" href="#">RESIDENTIAL SERVICES</a>
</div>
<div class="cat cat-com">
  <h2>COMMERCIAL</h2>
  <ul><li>Outdoor Office Landscapes</li><li>Hotels &amp; Hospitality</li><li>Event Venues</li><li>Parking Lot &amp; Security Lighting</li></ul>
  <a class="cat-btn" href="#">COMMERCIAL SERVICES</a>
</div>
<div class="cat-photo" style="left:883px;background:linear-gradient(170deg,#2d3d57,#5a5b66 40%,#c29a5e 65%,#2c3a22)" role="img" aria-label="Large home lit at night with glowing driveway"></div>
<div class="badge">CORWIN<br>BEACON<br>LIGHTING</div>

<div class="watermark-v">CORWIN</div>
<div class="about">
  <h2>ABOUT US</h2>
  <p>At <b>Corwin Beacon Lighting</b>, we believe that the right lighting doesn't just brighten a space — it transforms it. For over 20 years, we've been helping homeowners and businesses bring their outdoor environments to life through expertly designed and installed landscape lighting solutions.</p>
  <p>From intimate backyard retreats to large-scale commercial properties, our team blends creativity with technical precision to highlight your property's best features, enhance safety, and create unforgettable ambiance after dark.</p>
  <a class="btn" href="#">LEARN MORE</a>
</div>
<div class="about-frame"></div>
<div class="about-photo" role="img" aria-label="Stone house with uplit trees and a lit garden walkway"></div>

<section class="stats">
  <div class="stat" style="left:134px">
    <div class="ring"><svg width="38" height="38" viewBox="0 0 40 40" fill="none" stroke="#00AB8E" stroke-width="2"><path d="M20 6l10 4v8c0 7-5 12-10 14-5-2-10-7-10-14v-8z"/><path d="M15 19l4 4 7-8"/></svg></div>
    <div class="num">09+</div><div class="lbl">Core Values</div>
  </div>
  <div class="divider" style="left:358px"></div>
  <div class="stat" style="left:380px">
    <div class="ring"><svg width="38" height="38" viewBox="0 0 40 40" fill="none" stroke="#00AB8E" stroke-width="2"><circle cx="20" cy="13" r="4"/><circle cx="10" cy="17" r="3"/><circle cx="30" cy="17" r="3"/><path d="M12 30c0-5 4-9 8-9s8 4 8 9M4 30c0-4 3-7 6-7M36 30c0-4-3-7-6-7"/></svg></div>
    <div class="num">4.2k</div><div class="lbl">Experience</div>
  </div>
  <div class="divider" style="left:596px"></div>
  <div class="stat" style="left:623px">
    <div class="ring"><svg width="38" height="38" viewBox="0 0 40 40" fill="none" stroke="#00AB8E" stroke-width="2"><rect x="8" y="6" width="20" height="26" rx="2"/><path d="M12 12h12M12 17h12M12 22h6"/><circle cx="28" cy="27" r="5"/></svg></div>
    <div class="num">1,000+</div><div class="lbl">Certifications</div>
  </div>
  <div class="divider" style="left:832px"></div>
  <div class="stat" style="left:861px">
    <div class="ring"><svg width="38" height="38" viewBox="0 0 40 40" fill="none" stroke="#00AB8E" stroke-width="2"><circle cx="20" cy="17" r="5"/><path d="M10 32c0-6 4-10 10-10s10 4 10 10M20 4v4M8 10l3 3M32 10l-3 3"/></svg></div>
    <div class="num">5,000+</div><div class="lbl">Customer approach</div>
  </div>
</section>

<h2 class="section-title" style="top:1788px">OUR LIGHTING SERVICES</h2>
<div class="svc" style="left:121px"><div class="ph" role="img" aria-label="Tree-lined brick walkway with ground lights" style="background:linear-gradient(180deg,#1d2b2c,#3a3d30 50%,#a0724a 85%)"></div><div class="label">PATHWAY WALKWAY LIGHTING</div></div>
<div class="svc" style="left:447px"><div class="ph" role="img" aria-label="Garden dining table under lanterns in trees" style="background:linear-gradient(180deg,#1c2a1c,#4a4128 50%,#b5833e 80%,#1f2c18)"></div><div class="label">GARDEN TREE LIGHTING</div></div>
<div class="svc" style="left:770px"><div class="ph" role="img" aria-label="Backyard lounge with string lights over a lawn" style="background:linear-gradient(180deg,#1c2620,#3b4a33 45%,#a89060 70%,#4e7a2a)"></div><div class="label">OUTDOOR LIVING LIGHTING</div></div>

<h2 class="section-title" style="top:2225px">FEATURED PROJECTS</h2>
<div class="slide" style="left:0;width:127px;background:linear-gradient(180deg,#25301f,#5c4e30 50%,#2a3320)" role="img" aria-label="Garden lit by string lights"></div>
<div class="slide" style="left:135px;width:468px;background:linear-gradient(180deg,#4b5a8a 0%,#c69a8a 30%,#6b5a4a 60%,#3d6a2a 85%,#2d5220)" role="img" aria-label="Single-storey home at sunset with lit windows and lawn">
  <div class="proj-label" style="left:146px">PROJECT-1</div>
</div>
<div class="slide" style="left:609px;width:468px;background:linear-gradient(180deg,#34465e 0%,#4e5b6b 40%,#a2876a 65%,#2e4a24 90%)" role="img" aria-label="Modern two-storey house lit at dusk">
  <div class="proj-label" style="left:146px">PROJECT-2</div>
</div>
<div class="slide" style="left:1084px;width:116px;background:linear-gradient(180deg,#2c3b2e,#516a3a 60%,#3e5a28)" role="img" aria-label="Lit garden with shrubs"></div>
<div class="arrow" style="left:59px"><svg width="12" height="12" viewBox="0 0 12 12" fill="none" stroke="#fff" stroke-width="1.5"><path d="M8 2L4 6l4 4"/></svg></div>
<div class="arrow" style="left:1107px"><svg width="12" height="12" viewBox="0 0 12 12" fill="none" stroke="#fff" stroke-width="1.5"><path d="M4 2l4 4-4 4"/></svg></div>
<a class="btn explore" href="#">EXPLORE ALL PROJECTS</a>

<div class="quote-box">
  <div class="quote-mark">”</div>
  <div class="stars">★★★★★</div>
  <div class="q-name">— MARCUS ELLERY</div>
  <div class="q-role">Real Estate Investor</div>
  <p class="q-text">“The team was professional from start to finish. Our garden now looks stunning at night, and we've had so many compliments from neighbors. Highly recommend for anyone wanting high-quality outdoor lighting.They designed a lighting setup that perfectly fits our style.”</p>
</div>
<div class="quote-photo" role="img" aria-label="Client in a dark suit giving a thumbs up, video testimonial">
  <div class="play"><svg width="20" height="22" viewBox="0 0 20 22"><path d="M2 1l17 10L2 21z" fill="#00AB8E"/></svg></div>
</div>

<section class="cta" role="img" aria-label="Home exterior lit at night">
  <h2>INSPIRED BY LIGHT, DESIGNED FOR IMPACT</h2>
  <p>Book your free on-site consultation and see how we can elevate your outdoor space.</p>
  <a class="btn" href="#">GET A FREE QUOTE</a>
</section>

<footer class="footer">
  <div class="f-brand">CORWIN BEACON LIGHTING</div>
  <p class="f-about">Lorem ipsum dolor sit amet, consectetur adipiscing elit. Nullam eget varius magna. Nunc et ultricies eros, ultricies interdum nisi. Mauris risus sapien, tempor sit amet</p>
  <div class="socials"><span></span><span></span><span></span></div>

  <h3 class="f-head" style="left:440px">MENU</h3>
  <ul class="f-menu"><li>Home</li><li>Services</li><li>Portfolio</li><li>About</li><li>Contact</li></ul>

  <h3 class="f-head" style="left:588px">CONTACT INFO</h3>
  <div class="f-contact">
    <div><span class="ci"><svg width="12" height="12" viewBox="0 0 24 24" fill="#fff"><path d="M12 2a7 7 0 0 0-7 7c0 5 7 13 7 13s7-8 7-13a7 7 0 0 0-7-7zm0 9.5a2.5 2.5 0 1 1 0-5 2.5 2.5 0 0 1 0 5z"/></svg></span><span>Gate 4, Unit 210 88 Linden<br>Street, Ashgrove West 2190</span></div>
    <div><span class="ci"><svg width="12" height="12" viewBox="0 0 24 24" fill="#fff"><path d="M6.6 10.8a15 15 0 0 0 6.6 6.6l2.2-2.2a1 1 0 0 1 1-.25 11.4 11.4 0 0 0 3.6.57 1 1 0 0 1 1 1V20a1 1 0 0 1-1 1A17 17 0 0 1 3 4a1 1 0 0 1 1-1h3.5a1 1 0 0 1 1 1c0 1.25.2 2.45.57 3.57a1 1 0 0 1-.25 1z"/></svg></span><span style="padding-top:5px">(02) 5550 1274</span></div>
    <div><span class="ci"><svg width="12" height="12" viewBox="0 0 24 24" fill="#fff"><path d="M2 11l20-8-6 18-4-7z"/></svg></span><span style="color:var(--yellow);padding-top:5px">info@corwinbeacon.com</span></div>
  </div>

  <h3 class="f-head" style="left:872px">NEWSLETTER</h3>
  <div class="f-news">
    <div>Subscribe to our newsletter</div>
    <div class="field">Enter email</div>
    <a class="btn" href="#">SUBSCRIBE</a>
  </div>

  <div class="copyright">Copyright © 2025 CORWIN BEACON LIGHTING. All Rights Reserved.</div>
  <div class="f-watermark">CORWIN BEACON LIGHTING</div>
</footer>

</body>
</html>
```